Black Matte card with samurai logo which I would like it to be textured and company name on one side and on the other side I would like the company information with the reno (Face logo) Sushi logo. Double Sided card.

majority customers are University students, University sororities and fraternities.

It Company

Reno Sushi
317 W. Harlow Ave
Tucson, AZ 85042
Phone (520)413-6271
Fax (520)357-1846
E-mail: Renosushidesert@mailbox-example.com
FB: Renosushidesert
Twitter: Renosushidesert

• Present Normal

```html
<!DOCTYPE html>
<html lang="en">
<head>
<meta charset="utf-8">
<title>Reno Sushi – Business Card</title>
<link rel="stylesheet" href="https://fonts.googleapis.com/css2?family=Open+Sans:wght@400;600&display=swap">
<style>
  :root {
    --page: #ecebe8;
    --ink: #3d3d3d;
    --ink-soft: #5a5a5a;
    --red: #b8302a;
    --red-bright: #e4222a;
    --black: #1c1c1c;
    --matte-light: #2e3132;
    --matte-dark: #070808;
    --white: #ffffff;
    --rule: #c9c9c9;
  }
  * { box-sizing: border-box; margin: 0; padding: 0; }
  html, body {
    width: 1200px; height: 1160px; overflow: hidden;
    background: var(--page);
    font-family: "Open Sans", Arial, sans-serif;
  }
  .sheet { position: relative; width: 1200px; height: 1160px; }

  .card {
    position: absolute;
    width: 820px; height: 468px;
    overflow: hidden;
    box-shadow: 0 6px 18px rgba(0,0,0,.18);
  }

  /* Front */
  .card--front {
    left: 60px; top: 60px;
    background:
      repeating-linear-gradient(0deg, rgba(255,255,255,.025) 0 2px, transparent 2px 4px),
      repeating-linear-gradient(90deg, rgba(0,0,0,.12) 0 1px, transparent 1px 3px),
      radial-gradient(ellipse 70% 60% at 50% 30%, var(--matte-light), var(--matte-dark));
    display: flex; align-items: center; justify-content: center;
  }
  .front-brand {
    display: flex; align-items: center; gap: 34px;
    color: var(--red-bright);
    font-weight: 400; font-size: 78px; letter-spacing: 1px;
    margin-top: -40px;
  }
  .front-brand .mark-dot {
    width: 64px; height: 64px; border-radius: 50%;
    background: var(--red-bright);
  }

  /* Back */
  .card--back {
    left: 320px; top: 620px;
    background: var(--white);
    border: 1px solid #d6d6d6;
  }
  .back-brand {
    position: absolute; left: 70px; top: 90px; width: 260px;
    display: flex; flex-direction: column; align-items: center; gap: 26px;
  }
  .back-brand .mark-dot {
    width: 110px; height: 110px; border-radius: 50%;
    background: var(--red);
  }
  .back-brand .name {
    color: var(--red); font-weight: 400; font-size: 46px; line-height: 1;
  }
  .divider {
    position: absolute; left: 358px; top: 72px;
    width: 1px; height: 270px; background: var(--rule);
  }
  .contact {
    position: absolute; left: 378px; top: 78px;
    list-style: none; color: var(--ink); font-size: 20px;
  }
  .contact li { display: flex; align-items: center; gap: 10px; height: 31px; }
  .contact svg { width: 18px; height: 18px; flex: none; }
  .contact .sq { width: 17px; height: 17px; background: var(--ink-soft); border-radius: 2px; flex: none; }
  .address {
    position: absolute; left: 378px; top: 268px;
    color: var(--ink); font-size: 20px; line-height: 31px;
  }
  .wave { position: absolute; left: 0; bottom: 0; width: 820px; height: 120px; }
</style>
</head>
<body>
<main class="sheet">

  <section class="card card--front" aria-label="Card front">
    <div class="front-brand">
      <span>reno</span>
      <span class="mark-dot" aria-hidden="true"></span>
      <span>sushi</span>
    </div>
  </section>

  <section class="card card--back" aria-label="Card back">
    <div class="back-brand">
      <span class="mark-dot" aria-hidden="true"></span>
      <span class="name">Reno Sushi</span>
    </div>

    <div class="divider"></div>

    <ul class="contact">
      <li>
        <svg viewBox="0 0 20 20" aria-hidden="true"><circle cx="10" cy="10" r="9" fill="none" stroke="var(--red)" stroke-width="1.6"/><path d="M7 5.5l2 2-1 1.5c.6 1.4 1.6 2.4 3 3l1.5-1 2 2-1.3 1.5c-3.5-.3-6.7-3.5-7-7z" fill="var(--red)"/></svg>
        (520)413-6271
      </li>
      <li>
        <svg viewBox="0 0 20 20" aria-hidden="true"><rect x="5.5" y="2" width="9" height="16" rx="1.5" fill="var(--red)"/><rect x="7" y="4" width="6" height="6" fill="var(--white)"/><circle cx="10" cy="14.5" r="1.2" fill="var(--white)"/></svg>
        (520)357-1846
      </li>
      <li>
        <svg viewBox="0 0 20 20" aria-hidden="true"><rect x="2" y="5" width="16" height="11" rx="1" fill="var(--red)"/><path d="M2.5 5.5L10 11l7.5-5.5" fill="none" stroke="var(--white)" stroke-width="1.4"/></svg>
        Renosushidesert@mailbox-example.com
      </li>
      <li><span class="sq" aria-hidden="true"></span>Renosushidesert</li>
      <li><span class="sq" aria-hidden="true"></span>Renosushidesert</li>
    </ul>

    <p class="address">Reno Sushi 317 W. Harlow Ave Tucson<br>AZ 85042</p>

    <svg class="wave" viewBox="0 0 820 120" preserveAspectRatio="none" aria-hidden="true">
      <path d="M0 0 C 90 70, 240 78, 420 60 C 600 42, 740 50, 820 78 L820 120 L0 120 Z" fill="var(--red)"/>
      <path d="M0 22 C 100 86, 260 90, 440 72 C 610 56, 750 62, 820 86 L820 120 L0 120 Z" fill="var(--white)"/>
      <path d="M0 32 C 110 92, 270 96, 450 80 C 620 66, 755 70, 820 92 L820 120 L0 120 Z" fill="var(--black)"/>
    </svg>
  </section>

</main>
</body>
</html>
```